Building company buisness cards

We are looking for a sharp modern new look for our business cards.
We are a New Zealand based company that specialises in house and land packages.
We have attached a photo of the current logo and would like to see if it can be improved somehow if needed.
We are open to any colours but we have chosen green at this stage.
Feel free to change the font and make the logo smarter looking.
Play with the colours and see what looks best.

We want a card that looks so good know one will want to throw it away!

Target Market(s)

Home buyers

Industry/Entity Type

Building

Contact Information for Business Card

Derek Tolvane
0217394062
dtolvane@quillmarkhomesteads.co.nz
quillmarkhomesteads.co.nz

Font styles to use
Serif
Sans Serif

Colors

Designer to choose colors to be used in the design.

Requirements
Must have
• Logo and company name on one side, details on the other side
Nice to have
• Color codes for the original green are HEX #4a8028, RGB(74,128,40), CMYK(42,0,69,50)
• Round corners, Raised and/or spot UV

```html
<!DOCTYPE html>
<html lang="en">
<head>
<meta charset="utf-8">
<title>Quillmark Homesteads – Business Cards</title>
<link rel="stylesheet" href="https://fonts.googleapis.com/css2?family=Roboto:wght@400;500;700&display=swap">
<style>
  :root {
    --brand-green: #4a8028;
    --ink-grey: #555555;
    --rule-grey: #c9c9c9;
    --card-white: #ffffff;
    --card-black: #050505;
    --stage: #ececec;
    --name-white: #e8e8e8;
  }
  * { margin: 0; padding: 0; box-sizing: border-box; }
  html, body {
    width: 1200px;
    height: 712px;
    overflow: hidden;
    background: var(--stage);
    font-family: "Roboto", Arial, sans-serif;
  }
  .card-set {
    width: 1200px;
    height: 712px;
    display: flex;
    align-items: center;
    justify-content: center;
    gap: 40px;
  }
  .card {
    width: 540px;
    height: 310px;
    border-radius: 10px;
    position: relative;
    overflow: hidden;
    border-bottom: 5px solid var(--brand-green);
  }
  .card--front {
    background: var(--card-white);
    display: flex;
    align-items: center;
  }
  .card--back {
    background: var(--card-black);
    display: flex;
    align-items: center;
    justify-content: center;
  }
  .brand {
    width: 250px;
    display: flex;
    flex-direction: column;
    align-items: center;
    gap: 12px;
  }
  .brand__mark {
    width: 22px;
    height: 22px;
    border-radius: 50%;
    background: var(--brand-green);
  }
  .brand__name {
    font-weight: 500;
    font-size: 22px;
    letter-spacing: 2px;
    line-height: 1.2;
    text-align: center;
    text-transform: uppercase;
    color: var(--brand-green);
  }
  .card--back .brand__mark { background: var(--name-white); width: 28px; height: 28px; }
  .card--back .brand__name { color: var(--name-white); font-size: 30px; letter-spacing: 3px; }
  .card--back .brand { width: auto; gap: 16px; }
  .divider {
    width: 1px;
    height: 120px;
    background: var(--rule-grey);
  }
  .contact {
    padding-left: 30px;
  }
  .contact__name {
    font-weight: 700;
    font-size: 21px;
    color: var(--brand-green);
    text-transform: uppercase;
    margin-bottom: 14px;
  }
  .contact__line {
    font-size: 13px;
    color: var(--ink-grey);
    line-height: 1.45;
  }
</style>
</head>
<body>
  <main class="card-set">
    <section class="card card--front">
      <div class="brand">
        <span class="brand__mark"></span>
        <span class="brand__name">Quillmark<br>Homesteads</span>
      </div>
      <div class="divider"></div>
      <div class="contact">
        <p class="contact__name">Derek Tolvane</p>
        <p class="contact__line">0217394062</p>
        <p class="contact__line">dtolvane@quillmarkhomesteads.co.nz</p>
        <p class="contact__line">quillmarkhomesteads.co.nz</p>
      </div>
    </section>
    <section class="card card--back">
      <div class="brand">
        <span class="brand__mark"></span>
        <span class="brand__name">Quillmark<br>Homesteads</span>
      </div>
    </section>
  </main>
</body>
</html>
```